Music Producer Website

I need a website designed for my music production company. We specialize in finding talented musicians and matching them with music producers all over the United States. A visitor can create a profile and/or upload their music demo and we submit it to thousands of music producers and production companies for review. In many cases, our members will receive multiple signing offers from music producers allowing them to choose the contract that is best for them. "We turn aspiring musicians into SuperStars!"
Please include photos that reflect all genres of music (black artists, white artists, both male and female.) We produce all types of music including rap, R&B, rock, country, and Hip Hop.
When a user creates a profile, they become visible to thousands of record producers who are looking to sign new talent and make them stars.
Somewhere in the top half of the page, please include a small form that the visitor can fill out. The form should look as follows:
Title (large and bold): Contact Us or Submit Music Demo
Fields to include (* = required): First Name*, Last Name*, Age, Zip Code, Email Address*, Daytime Phone, Evening Phone, Comments
Then, there will be a "submit" button to proceed to next step of form. Just below the "submit" button, should be the following verbiage: "After submitting, you will have the opportunity to upload demos of your music (optional) and provide other pertinent information about yourself, band, or group."
Updates
Reason: I have not seen a design that I am 100% satisfied with yet. Ideally, rotating header images (GIF or other) with several different music producers in studio (male, female, black, white) would be perfect. Here are some examples of how the header pics could look:
http://files.quillmarsh.net/art_img/514302/806421/806421_7391046_514302_image.jpg
http://files.quillmarsh.net/art_img/514302/806421/806421_7391058_514302_image.jpg
http://files.quillmarsh.net/art_img/514302/806421/806421_7391037_514302_image.jpg
Also, there should be a form on the site (somewhere in upper half of the page) with the following headline:
GET FOUND AND BECOME A STAR! (super large, super-bold font)
Contact Us or Submit Your Music for Review (large font, not as bold as headline)
First Name
Last Name
Age
Zip Code
Email Address
Daytime Phone
Evening Phone
Comments
Target Market(s)
We are targeting all types of musicians including rock, rap, pop, R&B, country, gospel, etc.
Industry/Entity Type
Artists
Colors
Designer to choose colors to be used in the design.
Look and feel
Each slider illustrates characteristics of the customer's brand and the style your logo design should communicate.

```html
<!DOCTYPE html>
<html lang="en">
<head>
<meta charset="utf-8">
<title>Verano Music Productions</title>
<link href="https://fonts.googleapis.com/css2?family=Cinzel:wght@400;700&family=PT+Sans+Narrow:wght@400;700&display=swap" rel="stylesheet">
<style>
:root{
  --black:#000;
  --ink:#0b0906;
  --gold:#c9a75a;
  --gold-dark:#7a5f1f;
  --gold-deep:#5e4a18;
  --gold-text:#d4b262;
  --field:#6b531b;
  --field-text:#d8bf85;
  --muted:#b89c5c;
  --white:#f2ead8;
}
*{box-sizing:border-box;margin:0;padding:0}
html,body{width:793px;height:1200px;overflow:hidden;background:var(--black)}
body{position:relative;font-family:"PT Sans Narrow",sans-serif;color:var(--muted)}
.abs{position:absolute}
.caps{font-family:"Cinzel",serif;letter-spacing:.5px}

.site-header{left:0;top:0;width:793px;height:78px;background:var(--black)}
.brand{left:58px;top:0;width:164px;height:78px;background:#141210;display:flex;flex-direction:column;align-items:center;justify-content:center}
.brand-name{font-family:"Cinzel",serif;font-size:25px;color:var(--gold);line-height:1}
.brand-sub{font-family:"Cinzel",serif;font-size:7.5px;letter-spacing:1.6px;color:var(--gold);margin-top:3px}
.main-nav{top:44px;left:316px;display:flex;gap:16px;font-size:11px;color:var(--gold-text)}
.main-nav span:first-child{margin-right:6px}
.account{top:14px;display:flex;gap:4px;left:597px}
.account span{display:block;width:53px;height:16px;font-family:"Cinzel",serif;font-size:7.5px;text-align:center;line-height:16px;color:#222}
.btn-signup{background:linear-gradient(#fff,#bbb)}
.btn-login{background:linear-gradient(#f0d884,#b89336)}

.hero{left:0;top:78px;width:793px;height:332px;background:radial-gradient(ellipse at 40% 45%,#6d1a12 0%,#2b1320 30%,#0e0f22 60%,#050508 100%)}
.tagline{left:109px;top:228px;font-family:"Cinzel",serif;font-size:12.5px;color:#fff}
.demo-title{left:521px;top:103px;font-family:"Cinzel",serif;font-size:10px;color:var(--gold-text)}
.demo-form{left:522px;top:122px;width:185px;height:256px;background:linear-gradient(#8c6d24,#6d5418);border:1px solid #a78a3e}
.field{position:absolute;background:var(--field);border:1px solid #5a4513;font-size:8.5px;color:var(--field-text);padding:5px 6px}
.submit{position:absolute;left:55px;top:225px;width:75px;height:20px;background:linear-gradient(#e9c46b,#a5801f);font-weight:700;font-size:9px;color:#2a1c00;text-align:center;line-height:20px;border-radius:2px}
.slider-track{left:80px;top:389px;width:626px;height:9px;border-radius:5px;background:linear-gradient(#a48746,#5c4717)}
.slider-thumb{left:80px;top:389px;width:40px;height:9px;border-radius:5px;background:#4a3a12}

.partners{left:0;top:410px;width:793px;height:57px;background:var(--gold);display:flex;align-items:center;justify-content:center;gap:26px}
.partner{background:#1c160a;opacity:.85}

.section-title{font-family:"Cinzel",serif;font-size:10.5px;color:var(--gold-text);letter-spacing:.8px}
.arrow{width:16px;height:13px;background:linear-gradient(#e6c66c,#a8842a);display:flex;align-items:center;justify-content:center}

.photo{position:absolute;border:1px solid #8a7038;display:flex;align-items:center;justify-content:center}
.play{width:22px;height:22px;border-radius:50%;background:rgba(20,20,20,.75);border:2px solid #fff;display:flex;align-items:center;justify-content:center}
.play::after{content:"";border-left:7px solid #fff;border-top:5px solid transparent;border-bottom:5px solid transparent;margin-left:2px}
.caption{position:absolute;font-size:8px;line-height:14px;color:var(--muted);width:110px}

.pager{left:191px;top:1104px;display:flex;gap:5px}
.pager span{height:16px;min-width:17px;padding:0 5px;background:linear-gradient(#ecd085,#b38f35);font-size:8px;line-height:16px;text-align:center;color:#3a2a06}

.item-title{font-size:10px;color:var(--gold-text)}
.item-body{font-size:8px;color:#ddd;line-height:13px;margin-top:6px}
.read-more{width:57px;height:20px;background:linear-gradient(#e6c770,#a68526);font-family:"Cinzel",serif;font-size:7px;line-height:20px;text-align:center;color:#2c1f00}
.review-text{font-size:8px;color:var(--muted);line-height:16px;width:150px}
.stars{display:flex;gap:4px;margin-top:8px}

.site-footer{left:0;top:1146px;width:793px;height:54px;background:var(--gold)}
.foot-nav{left:86px;top:10px;font-family:"Cinzel",serif;font-size:8.5px;color:#2a1e06;word-spacing:2px}
.copyright{left:88px;top:32px;font-family:"Cinzel",serif;font-size:7.5px;color:#2a1e06}
.social{position:absolute;top:17px;width:22px;height:22px;border-radius:50%;background:#111}
</style>
</head>
<body>

<header class="site-header abs">
  <div class="brand abs"><div class="brand-name">VERANO</div><div class="brand-sub">MUSIC PRODUCTIONS</div></div>
  <nav class="main-nav abs caps"><span>Home</span><span>About Us</span><span>Create A Profile</span><span>Music Producers</span><span>Contact Us</span></nav>
  <div class="account abs"><span class="btn-signup">SIGN UP</span><span class="btn-login">LOGIN</span></div>
</header>

<section class="hero abs" role="img" aria-label="Stage photo: singer in red dress at a microphone with guitarist and violinist">
</section>
<div class="tagline abs">We turn aspiring musicians into SuperStars!</div>
<div class="demo-title abs">Submit Music Demo</div>
<form class="demo-form abs">
  <div class="field" style="left:10px;top:10px;width:163px;height:21px">First Name</div>
  <div class="field" style="left:10px;top:37px;width:163px;height:21px">Last Name</div>
  <div class="field" style="left:10px;top:62px;width:163px;height:21px">E-Mail</div>
  <div class="field" style="left:10px;top:87px;width:47px;height:21px">Age</div>
  <div class="field" style="left:64px;top:87px;width:109px;height:21px">Zip-Code</div>
  <div class="field" style="left:10px;top:114px;width:163px;height:21px">Daytime Phone</div>
  <div class="field" style="left:10px;top:140px;width:163px;height:21px">Evening Phone</div>
  <div class="field" style="left:10px;top:167px;width:163px;height:51px">Comments</div>
  <div class="submit">SUBMIT</div>
</form>
<div class="slider-track abs"></div>
<div class="slider-thumb abs"></div>

<section class="partners abs" aria-label="Partners">
  <div class="partner" style="width:46px;height:40px;border-radius:50% 50% 4px 4px"></div>
  <div class="partner" style="width:62px;height:30px"></div>
  <div class="partner" style="width:48px;height:36px"></div>
  <div class="partner" style="width:64px;height:26px"></div>
  <div class="partner" style="width:40px;height:40px;border-radius:50%"></div>
  <div class="partner" style="width:88px;height:18px"></div>
  <div class="partner" style="width:106px;height:16px"></div>
</section>

<h2 class="section-title abs" style="left:80px;top:483px">Latest Uploaded Music Demos</h2>
<div class="abs" style="left:394px;top:483px;display:flex;gap:4px">
  <div class="arrow"><svg width="8" height="8"><path d="M6 0L1 4l5 4z" fill="#2a1e06"/></svg></div>
  <div class="arrow"><svg width="8" height="8"><path d="M2 0l5 4-5 4z" fill="#2a1e06"/></svg></div>
</div>

<div class="demo-grid">
  <div class="photo" style="left:86px;top:516px;width:106px;height:82px;background:linear-gradient(135deg,#1d4b6b,#0b1420)" role="img" aria-label="Rock singer on stage"><span class="play"></span></div>
  <div class="photo" style="left:205px;top:516px;width:106px;height:82px;background:linear-gradient(135deg,#7a3d8a,#d9a26a)" role="img" aria-label="Pop singer with microphone"><span class="play"></span></div>
  <div class="photo" style="left:323px;top:516px;width:107px;height:82px;background:linear-gradient(135deg,#ddd,#222)" role="img" aria-label="Singer in black and white"><span class="play"></span></div>
  <div class="photo" style="left:86px;top:665px;width:106px;height:82px;background:linear-gradient(135deg,#2a4a8a,#6b4a2a)" role="img" aria-label="Rapper performing"><span class="play"></span></div>
  <div class="photo" style="left:205px;top:665px;width:106px;height:82px;background:linear-gradient(135deg,#aaa,#111)" role="img" aria-label="Male vocalist at microphone"><span class="play"></span></div>
  <div class="photo" style="left:323px;top:665px;width:107px;height:82px;background:linear-gradient(135deg,#6a4a3a,#151010)" role="img" aria-label="Female singer on dark stage"><span class="play"></span></div>
  <div class="photo" style="left:86px;top:810px;width:106px;height:81px;background:linear-gradient(135deg,#c65a2a,#4a5a8a)" role="img" aria-label="Singer with orange hair"><span class="play"></span></div>
  <div class="photo" style="left:205px;top:810px;width:106px;height:81px;background:linear-gradient(135deg,#3a5a8a,#c9a070)" role="img" aria-label="Blonde singer performing"><span class="play"></span></div>
  <div class="photo" style="left:323px;top:810px;width:107px;height:81px;background:linear-gradient(135deg,#c67a2a,#111)" role="img" aria-label="Performer under stage lights"><span class="play"></span></div>
  <div class="photo" style="left:86px;top:964px;width:106px;height:82px;background:linear-gradient(135deg,#6a5a4a,#2a2018)" role="img" aria-label="Musician in studio"><span class="play"></span></div>
  <div class="photo" style="left:205px;top:964px;width:106px;height:82px;background:linear-gradient(135deg,#3a2aa0,#e04ac0)" role="img" aria-label="Singer under pink lights"><span class="play"></span></div>
  <div class="photo" style="left:323px;top:964px;width:107px;height:82px;background:linear-gradient(135deg,#555,#050505)" role="img" aria-label="Singer portrait in dark"><span class="play"></span></div>

  <div class="caption" style="left:86px;top:603px">Name : Milo Trent<br>Song : I will also be<br>&nbsp;Time : 1.45</div>
  <div class="caption" style="left:205px;top:603px">Name : Milo Trent<br>Song : I will also be<br>&nbsp;Time : 1.45</div>
  <div class="caption" style="left:323px;top:603px">Name : Milo Trent<br>Song : I will also be<br>&nbsp;Time : 1.45</div>
  <div class="caption" style="left:86px;top:752px">Name : Milo Trent<br>Song : I will also be<br>&nbsp;Time : 1.45</div>
  <div class="caption" style="left:205px;top:752px">Name : Milo Trent<br>Song : I will also be<br>&nbsp;Time : 1.45</div>
  <div class="caption" style="left:323px;top:752px">Name : Milo Trent<br>Song : I will also be<br>&nbsp;Time : 1.45</div>
  <div class="caption" style="left:86px;top:900px">Name : Milo Trent<br>Song : I will also be<br>&nbsp;Time : 1.45</div>
  <div class="caption" style="left:205px;top:900px">Name : Milo Trent<br>Song : I will also be<br>&nbsp;Time : 1.45</div>
  <div class="caption" style="left:323px;top:900px">Name : Milo Trent<br>Song : I will also be<br>&nbsp;Time : 1.45</div>
  <div class="caption" style="left:86px;top:1052px">Name : Milo Trent<br>Song : I will also be<br>&nbsp;Time : 1.45</div>
  <div class="caption" style="left:205px;top:1052px">Name : Milo Trent<br>Song : I will also be<br>&nbsp;Time : 1.45</div>
  <div class="caption" style="left:323px;top:1052px">Name : Milo Trent<br>Song : I will also be<br>&nbsp;Time : 1.45</div>
</div>

<nav class="pager abs"><span>Prev</span><span>1</span><span>2</span><span>3</span><span>4</span><span>5</span><span>6</span><span>…</span><span>22</span><span>Next</span></nav>

<h2 class="section-title abs" style="left:472px;top:483px">List of Selected Musics</h2>
<div class="photo" style="left:475px;top:518px;width:67px;height:60px;background:linear-gradient(135deg,#b02a1a,#1a0a08)" role="img" aria-label="Vocalist in red light"><span class="play"></span></div>
<div class="photo" style="left:475px;top:603px;width:67px;height:60px;background:linear-gradient(135deg,#d08a2a,#5a4a2a)" role="img" aria-label="Singer in warm light"><span class="play"></span></div>
<div class="photo" style="left:475px;top:688px;width:67px;height:60px;background:linear-gradient(135deg,#8a2a3a,#151515)" role="img" aria-label="Singer on stage"><span class="play"></span></div>
<div class="abs" style="left:551px;top:526px;width:150px"><div class="item-title">Neque porro quisquam est qui</div><div class="item-body">Lorem Ipsum is simply dummy text of the printing and typesetting industry.</div></div>
<div class="abs" style="left:551px;top:611px;width:150px"><div class="item-title">Neque porro quisquam est qui</div><div class="item-body">Lorem Ipsum is simply dummy text of the printing and typesetting industry.</div></div>
<div class="abs" style="left:551px;top:696px;width:150px"><div class="item-title">Neque porro quisquam est qui</div><div class="item-body">Lorem Ipsum is simply dummy text of the printing and typesetting industry.</div></div>
<div class="read-more abs" style="left:649px;top:769px">READ MORE</div>

<h2 class="section-title abs" style="left:473px;top:823px">Latest Reviews</h2>
<div class="photo" style="left:472px;top:856px;width:67px;height:58px;background:linear-gradient(135deg,#7a8aa0,#2a2a2a)" role="img" aria-label="Reviewed artist performing"></div>
<div class="photo" style="left:472px;top:945px;width:67px;height:59px;background:linear-gradient(135deg,#d0603a,#e0c0a0)" role="img" aria-label="Reviewed singer close-up"></div>
<div class="photo" style="left:472px;top:1025px;width:67px;height:59px;background:linear-gradient(135deg,#c03a3a,#2a0a0a)" role="img" aria-label="Reviewed performer on stage"></div>

<div class="abs" style="left:560px;top:851px"><div class="review-text">Sed ut perspiciatis unde omnis iste natus error sit voluptatem accusantium</div>
  <div class="stars"><svg width="90" height="15" viewBox="0 0 90 15"><g fill="#c9a75a"><path id="st" d="M7.5 0l2 5h5.3l-4.3 3.3 1.7 5.4-4.7-3.3-4.7 3.3 1.7-5.4L.2 5h5.3z"/><use href="#st" x="19"/><use href="#st" x="38"/><use href="#st" x="57"/><use href="#st" x="76"/></g></svg></div></div>
<div class="abs" style="left:560px;top:939px"><div class="review-text">Sed ut perspiciatis unde omnis iste natus error sit voluptatem accusantium</div>
  <div class="stars"><svg width="90" height="15" viewBox="0 0 90 15"><g fill="#c9a75a"><use href="#st"/><use href="#st" x="19"/><use href="#st" x="38"/><use href="#st" x="57"/><use href="#st" x="76"/></g></svg></div></div>
<div class="abs" style="left:560px;top:1026px"><div class="review-text">Sed ut perspiciatis unde omnis iste natus error sit voluptatem accusantium</div>
  <div class="stars"><svg width="90" height="15" viewBox="0 0 90 15"><g fill="#c9a75a"><use href="#st"/><use href="#st" x="19"/><use href="#st" x="38"/><use href="#st" x="57"/><use href="#st" x="76"/></g></svg></div></div>
<div class="read-more abs" style="left:649px;top:1102px">READ MORE</div>

<footer class="site-footer abs">
  <div class="foot-nav abs">Home &nbsp;| &nbsp;About Us &nbsp;| &nbsp;Create A Profile &nbsp;| &nbsp;Music Producers &nbsp;| &nbsp;Contact Us</div>
  <div class="copyright abs">Copyright ©2013 Company Name &nbsp;- All Rights Reserved</div>
  <span class="social" style="left:634px"></span>
  <span class="social" style="left:660px"></span>
  <span class="social" style="left:685px"></span>
</footer>

</body>
</html>
```